Brochure for a website accessibility report

This brochure is related to a report that www.qelvantrix.org sell. The report shows the results of an automated audit of a websites accessibility. It shows details of issues found with screen shots, examples of code and provides remediation advice.

The brochure will be a pdf 8.5 inches by 11 inches. It can be anywhere from 6 to 10 pages.

The FlintVue™ name itself should be “Bree Serif” font. The fonts, styles, colors and sizes are up to you.

The images used and logo of the Office of Digital Reachworks and K7P logo are upload

We highlighted in blue page extracts from the report we sell. Do not use the blue highlight, it is merely there to show you where the specific examples of the report we sell are vs the other content in the report. The areas in blue which show the content from the actual report should be shown as an extract of the actual page of the report. You have flexibility to change the layout and the way the content look.

The red square callouts over the blue content are callouts that describe the specific page extracts. We used it as a red callout only so that you would be able to see it. You should change the specific location, look and feel of the callout to be appropriate

Target Market(s)

Marketing and Technical people

Industry/Entity Type

Information Technology

Font styles to use
Sans Serif

Colors

Designer to choose colors to be used in the design.

Requirements
Should not have
• wheelchairs, images of blind people

```html
<!DOCTYPE html>
<html lang="en">
<head>
<meta charset="utf-8">
<title>FlintVue™ Report Overview</title>
<link rel="stylesheet" href="https://fonts.googleapis.com/css2?family=Arimo:ital,wght@0,400;0,700;1,400&family=Bree+Serif&display=swap">
<style>
  :root {
    --green: #2bb673;
    --green-text: #27a866;
    --green-faint: #d3ecdd;
    --panel: #e8f3ec;
    --ink: #1a1a1a;
    --paper: #ffffff;
  }
  * { box-sizing: border-box; margin: 0; padding: 0; }
  html, body { width: 1200px; height: 927px; overflow: hidden; background: var(--paper); }
  .page {
    position: relative; width: 1200px; height: 927px;
    font-family: "Arimo", Arial, sans-serif; color: var(--ink);
  }
  .brand {
    position: absolute; top: 10px; left: 1087px;
    display: flex; align-items: flex-start; gap: 5px;
  }
  .brand-mark { width: 18px; height: 18px; background: var(--green); margin-top: 2px; }
  .brand-name {
    font-weight: 700; font-size: 11px; line-height: 13px; color: var(--ink);
    text-transform: uppercase; letter-spacing: 0.2px;
  }
  .side-name {
    position: absolute; left: 1134px; top: 215px;
    writing-mode: vertical-rl;
    font-family: "Bree Serif", Georgia, serif; font-size: 74px; line-height: 66px;
    color: var(--green-faint); white-space: nowrap;
  }
  .body-text {
    position: absolute; left: 109px; width: 982px;
    font-size: 16.2px; line-height: 21.8px; text-align: justify;
  }
  .intro { top: 105px; }
  .partner {
    position: absolute; top: 226px; left: 0; width: 1200px;
    display: flex; justify-content: center; align-items: center; gap: 12px;
  }
  .partner-mark { width: 40px; height: 40px; background: #0a5aa0; }
  .partner-name { font-weight: 700; font-size: 30px; color: #0a5aa0; letter-spacing: 1px; }
  .lead {
    position: absolute; top: 304px; left: 0; width: 1200px; text-align: center;
    font-size: 19px; color: var(--green-text); text-decoration: underline;
    text-underline-offset: 3px;
  }
  .principles {
    position: absolute; top: 342px; left: 124px; width: 953px;
    display: grid; grid-template-columns: 1fr 1fr; grid-template-rows: 120px 100px;
    gap: 7px;
  }
  .principle { background: var(--panel); padding: 0 34px; text-align: center; }
  .principle h3 {
    font-size: 17.5px; line-height: 22px; font-weight: 700; color: var(--green-text);
  }
  .principle p { font-size: 15.4px; line-height: 20px; text-align: justify; text-align-last: center; }
  .principle em { font-style: italic; }
  .product { font-family: "Bree Serif", Georgia, serif; }
  .journey { top: 596px; }
  .sections { top: 681px; }
  .sections ul { list-style: none; margin-left: 48px; }
  .sections li { position: relative; }
  .sections li::before {
    content: ""; position: absolute; left: -19px; top: 6px;
    width: 10px; height: 10px; background: var(--green);
  }
  .page-number {
    position: absolute; left: 1091px; top: 818px; width: 109px; height: 109px;
    background: var(--green); color: var(--paper);
    display: flex; align-items: center; justify-content: center; font-size: 17px;
  }
</style>
</head>
<body>
<div class="page">
  <div class="brand">
    <div class="brand-mark"></div>
    <div class="brand-name">Office of<br>Digital<br>Reachworks</div>
  </div>

  <div class="side-name">FlintVue™</div>

  <p class="body-text intro">The Americans with Disabilities Act (ADA) is a comprehensive federal civil rights law prohibiting discrimination on the basis of disability, enforced by the Department of Justice (DOJ). The ADA prohibits discriminatory lack of access for individuals with disabilities to goods and services of public services and accommodations. Websites are considered places of public accommodations. The DOJ currently uses WCAG 2.1 Level A/AA as an accepted standard by which to measure a website’s accessibility.</p>

  <div class="partner">
    <div class="partner-mark"></div>
    <div class="partner-name">K7P Standards Group</div>
  </div>

  <p class="lead">WCAG 2.1 Level A/AA consists of 13 guidelines with 50 checkpoints that are organized under four principles:</p>

  <div class="principles">
    <div class="principle">
      <h3>Principle 1: PERCEIVABLE</h3>
      <p>Information and user interface components must be presented to users in ways they can perceive. This means that users must be able to comprehend the information being depicted: It can’t be invisible to all their senses.</p>
    </div>
    <div class="principle">
      <h3>Principle 2: OPERABLE</h3>
      <p>User interface components and navigation must be operable: The interface cannot require interaction that a user cannot perform.</p>
    </div>
    <div class="principle">
      <h3>Principle 3: Understandable</h3>
      <p>Information and the operation of a user interface must be understandable: <em>Users must be able to understand the information as well as the operation of the user interface.</em></p>
    </div>
    <div class="principle">
      <h3>Principle 4: ROBUST</h3>
      <p>Content must be robust enough that it can be interpreted reliably by a wide variety of user agents, including assistive technologies: As technologies and user agents evolve, the content should remain accessible.</p>
    </div>
  </div>

  <p class="body-text journey">Start your journey to a fully compliant website with <span class="product">FlintVue™</span>. This detailed compliance and remediation report is generated based on scanning your website against hundreds of carefully-crafted rules, logging failures, and then generating feedback and recommendations on how to fix the problems based on our years of experience and proven best practices.</p>

  <div class="body-text sections">
    <p>The <span class="product">FlintVue™</span> report is designed to be shared with your executive team and stakeholders. It is divided into two sections to build knowledge and self-sufficiency.</p>
    <ul>
      <li>The first section provides a detailed analysis of your website per the WCAG 2.1 A/AA principles and includes an at-a-glance Summary Chart for your executive team.</li>
      <li>The second section is designed specifically for your website development team, providing them with detailed examples of problematic issues, suggested ways to fix them, and links for more detailed training.</li>
    </ul>
  </div>

  <div class="page-number">3</div>
</div>
</body>
</html>
```